Business Cards for IT Consulting Company (Managed Service Provider)

I am looking to have some business cards printed and would like some designs. We are an IT Consulting company based in Vancouver BC. I would like a nice clean and modern look to the cards. I have uploaded all the versions of my logo so parts can be used as needed. Here is a snippit from our website homepage:

Quillbrook Networks Ltd. is an IT Solutions Partner located in Vancouver BC, Canada. We offer IT solutions and support to customers in the greater Vancouver Area. With expertise in Microsoft platforms, as well as Linux and Mac OSX and over 12 years experience in the IT industry, Quillbrook Networks is dedicated to offering our clients top quality service and products. We take pride in the solutions we offer our customers. The greatest compliment a client can give us is to recommend our services.

Quillbrook Networks Ltd. offers a wide range of IT services from onsite service to remote support and managed service solutions. This allows clients to choose the support path that best suits their company’s needs. Supporting many different sized companies from small to enterprise level over the past 12 years Quillbrook Networks has the experience and expertise needed to ensure things run smoothly. Allowing our clients to focus on doing business.

Revolutionizing the way IT services are delivered.

Quillbrook Networks is dedicated to providing our clients with IT solutions that work and grow with them for years to come. This philosophy helps save money in the long run instead of replacing equipment constantly. Far too often IT solutions are not well thought out and while possibly solving the problem at hand, require replacement due to growth or quality within a very short time frame. Quillbrook Networks takes pride in providing solutions that will last and be able to accommodate growth without the need for replacement.

Industry/Entity Type

Information Technology

Contact Information for Business Card

Quillbrook Networks Ltd.
(Employee Name)
Eml: (Employees Email Address)
Web: quillbrook.me
Ph: 604-555-0148

Font styles to use
Serif
Sans Serif

Requirements
Must have
• The Company logo and company colors.
Nice to have
• - Our tag line: "Revolutionizing IT Services" or "Revolutionizing the way IT services are delivered."
• - Also I really like the idea of nature and technology together blending which is sort of where my logo came from so integrating that somehow onto the business cards would be great.

```html
<!DOCTYPE html>
<html lang="en">
<head>
<meta charset="utf-8">
<title>Quillbrook Networks – Business Cards</title>
<link rel="stylesheet" href="https://fonts.googleapis.com/css2?family=Open+Sans:wght@400;600;700&display=swap">
<style>
  :root {
    --backdrop: #3a3431;
    --card: #141414;
    --card-edge: #222222;
    --accent: #1aa3e0;
    --text-light: #d9d9d9;
    --text-muted: #9a9a9a;
    --divider: #5a5a5a;
    --brand: #e6e6e6;
  }
  * { box-sizing: border-box; margin: 0; padding: 0; }
  html, body {
    width: 1200px; height: 814px; overflow: hidden;
    background: var(--backdrop);
    font-family: "Open Sans", Arial, sans-serif;
  }
  .stage {
    position: relative; width: 1200px; height: 814px;
    display: flex; align-items: center; justify-content: center; gap: 48px;
  }
  .card {
    position: relative; width: 520px; height: 297px;
    background: var(--card);
    border: 1px solid var(--card-edge);
    box-shadow: 0 10px 28px rgba(0,0,0,.45);
  }
  /* contact side */
  .card-contact .brand-mark {
    position: absolute; left: 92px; top: 104px;
    width: 90px; height: 90px;
    border: 4px solid var(--accent);
  }
  .card-contact .divider {
    position: absolute; left: 258px; top: 60px;
    width: 1px; height: 178px; background: var(--divider);
  }
  .card-contact .details {
    position: absolute; left: 284px; top: 62px;
    color: var(--text-light); font-size: 13px; line-height: 20px;
  }
  .person-name {
    color: var(--accent); font-size: 20px; font-weight: 600;
    line-height: 28px; margin-bottom: 6px;
  }
  .address { margin-bottom: 4px; }
  .contact-line { display: flex; align-items: center; gap: 9px; }
  .contact-line svg { width: 12px; height: 12px; flex: none; fill: var(--accent); }
  /* logo side */
  .card-brand {
    display: flex; flex-direction: column; align-items: center; justify-content: center;
  }
  .brand-lockup { display: flex; align-items: center; gap: 16px; }
  .brand-square { width: 34px; height: 34px; background: var(--brand); }
  .brand-name {
    color: var(--brand); font-size: 30px; font-weight: 700; letter-spacing: .5px;
  }
  .tagline {
    margin-top: 22px; color: var(--text-light);
    font-size: 12px; font-weight: 600; letter-spacing: .2px;
  }
</style>
</head>
<body>
<main class="stage">
  <section class="card card-contact">
    <div class="brand-mark" aria-hidden="true"></div>
    <div class="divider"></div>
    <div class="details">
      <p class="person-name">Daniel Harper</p>
      <p class="address">1420 Cedar Row Lane<br>Vancouver, BC V5K 2A1</p>
      <p class="contact-line">
        <svg viewBox="0 0 24 24"><path d="M6.6 10.8a15.2 15.2 0 0 0 6.6 6.6l2.2-2.2c.3-.3.7-.4 1-.2 1.1.4 2.3.6 3.6.6.6 0 1 .4 1 1V20c0 .6-.4 1-1 1A17 17 0 0 1 3 4c0-.6.4-1 1-1h3.5c.6 0 1 .4 1 1 0 1.3.2 2.5.6 3.6.1.3 0 .7-.2 1z"/></svg>
        604-555-0148
      </p>
      <p class="contact-line">
        <svg viewBox="0 0 24 24"><path d="M2 5h20v14H2z M2 5l10 8 10-8" fill="none" stroke="#1aa3e0" stroke-width="2.4"/></svg>
        name@quillmail.com
      </p>
      <p class="contact-line">
        <svg viewBox="0 0 24 24"><circle cx="12" cy="12" r="10"/><path d="M2 12h20M12 2c3 3 3 17 0 20M12 2c-3 3-3 17 0 20" fill="none" stroke="#141414" stroke-width="1.6"/></svg>
        www.quillbrook.me
      </p>
    </div>
  </section>

  <section class="card card-brand">
    <div class="brand-lockup">
      <span class="brand-square" aria-hidden="true"></span>
      <span class="brand-name">Quillbrook Networks Ltd.</span>
    </div>
    <p class="tagline">Revolutionizing IT Services</p>
  </section>
</main>
</body>
</html>
```